Fun, Clean Business Card For Family Focused Travel Agency

I need a business card using specific colors and fonts as in the uploaded files. Ideally, I would like a large image of the logo on the back and all the contact info on the front. Maybe the stars/dots somewhere in a flowy form.

I do want it the contact information to be clear and easy to read. I don't want it to look too busy. Maybe even a bit minimalist.

I plan or ordering the ROUNDED CORNER business cards from Cardwell Press, so please consider that in your design.

Target Market(s)

Families with children, couples, groups of friends

Contact Information for Business Card

Marla Quint, Owner
Marla@TumbleTrips.example
Cell Phone Number 555-218-4603
Office Phone Number 555-647-1925
Specializing in Glimmerland destinations, Pelican Bay Fun Park, Cruises and All-Inclusive Vacations.

Nice but not required:
www.TumbleTrips.example
Facebook, Instagram, Twitter icons with username: TumbleTrips

Font styles to use
Sans Serif

Requirements
Must have
• Please try to use the colors from the logo as much as possible. I understand lighter shades/colors may be needed for some things.
Should not have
• NO SERIF FONTS. That is really the only thing I do not want at all

```html
<!DOCTYPE html>
<html lang="en">
<head>
<meta charset="utf-8">
<title>Tumble Trips — Business Card</title>
<link rel="stylesheet" href="https://fonts.googleapis.com/css2?family=Fira+Sans:wght@400;500;700&display=swap">
<style>
  :root {
    --navy: #1b1f40;
    --navy-deep: #141733;
    --teal: #15c3ad;
    --white: #ffffff;
    --paper: #f7f7f5;
    --stage: #e8e6e1;
    --soft-white: #d9dce8;
  }
  * { box-sizing: border-box; margin: 0; padding: 0; }
  html, body { width: 1200px; height: 780px; overflow: hidden; }
  body {
    background: var(--stage);
    font-family: "Fira Sans", Arial, sans-serif;
    display: flex;
    align-items: center;
    justify-content: center;
    gap: 40px;
  }
  .card {
    position: relative;
    width: 540px;
    height: 309px;
    border-radius: 18px;
    overflow: hidden;
    box-shadow: 0 6px 18px rgba(20, 23, 51, 0.18);
  }

  /* Front */
  .card-front { background: var(--paper); }
  .front-shapes { position: absolute; inset: 0; width: 100%; height: 100%; }
  .brand {
    position: absolute;
    display: flex;
    align-items: center;
    gap: 10px;
    font-weight: 700;
    white-space: nowrap;
  }
  .brand-dot { border-radius: 50%; background: var(--teal); flex: none; }
  .card-front .brand { left: 30px; top: 132px; font-size: 30px; color: var(--navy); }
  .card-front .brand-dot { width: 16px; height: 16px; }

  .contact {
    position: absolute;
    right: 30px;
    top: 40px;
    text-align: right;
    color: var(--white);
  }
  .contact-name { font-size: 22px; font-weight: 700; letter-spacing: 0.2px; }
  .contact-role { font-size: 14px; color: var(--teal); margin-top: 2px; }
  .contact-list { list-style: none; margin-top: 26px; }
  .contact-item {
    display: flex;
    align-items: center;
    justify-content: flex-end;
    gap: 10px;
    font-size: 14px;
    line-height: 1;
    margin-bottom: 12px;
  }
  .contact-icon {
    width: 22px; height: 22px;
    border-radius: 50%;
    background: var(--teal);
    border: 2px solid rgba(255,255,255,0.85);
    display: flex; align-items: center; justify-content: center;
    flex: none;
  }
  .contact-icon svg { width: 11px; height: 11px; }

  /* Back */
  .card-back {
    background: radial-gradient(ellipse at 55% 40%, #262b52 0%, var(--navy) 55%, var(--navy-deep) 100%);
  }
  .card-back .brand {
    left: 0; right: 0; top: 96px;
    justify-content: center;
    font-size: 40px;
    color: var(--white);
  }
  .card-back .brand-dot { width: 20px; height: 20px; }
  .specialty {
    position: absolute;
    left: 0; right: 0; top: 196px;
    text-align: center;
    color: var(--soft-white);
    font-size: 13px;
    line-height: 1.6;
  }
  .specialty strong { font-weight: 700; color: var(--white); }
</style>
</head>
<body>

  <section class="card card-front" aria-label="Card front">
    <svg class="front-shapes" viewBox="0 0 540 309" preserveAspectRatio="none" aria-hidden="true">
      <path d="M288 0 C 262 110, 225 215, 150 309 L 196 309 C 252 225, 282 120, 300 0 Z" fill="var(--teal)"/>
      <path d="M300 0 C 282 120, 252 225, 196 309 L 540 309 L 540 0 Z" fill="var(--navy)"/>
    </svg>

    <div class="brand">
      <span class="brand-dot"></span>
      <span class="brand-name">Tumble Trips</span>
    </div>

    <div class="contact">
      <p class="contact-name">Marla Quint</p>
      <p class="contact-role">Owner</p>
      <ul class="contact-list">
        <li class="contact-item">
          <span>555-218-4603</span>
          <span class="contact-icon">
            <svg viewBox="0 0 12 12"><rect x="3" y="0.8" width="6" height="10.4" rx="1.2" fill="none" stroke="#fff" stroke-width="1.3"/><circle cx="6" cy="9.2" r="0.7" fill="#fff"/></svg>
          </span>
        </li>
        <li class="contact-item">
          <span>555-647-1925</span>
          <span class="contact-icon">
            <svg viewBox="0 0 12 12"><path d="M2.6 1 L4.6 1 L5.4 3.4 L4.2 4.4 C4.8 5.8 6.2 7.2 7.6 7.8 L8.6 6.6 L11 7.4 L11 9.4 C11 10.4 10.2 11 9.2 11 C4.6 10.6 1.4 7.4 1 2.8 C1 1.8 1.6 1 2.6 1 Z" fill="#fff"/></svg>
          </span>
        </li>
        <li class="contact-item">
          <span>Marla@TumbleTrips.example</span>
          <span class="contact-icon">
            <svg viewBox="0 0 12 12"><rect x="1" y="2.5" width="10" height="7" rx="1" fill="none" stroke="#fff" stroke-width="1.3"/><path d="M1.5 3 L6 6.6 L10.5 3" fill="none" stroke="#fff" stroke-width="1.3"/></svg>
          </span>
        </li>
      </ul>
    </div>
  </section>

  <section class="card card-back" aria-label="Card back">
    <div class="brand">
      <span class="brand-dot"></span>
      <span class="brand-name">Tumble Trips</span>
    </div>
    <p class="specialty">
      <strong>Specializing in</strong> Glimmerland destinations<br>
      Pelican Bay Fun Park | Cruises and All-Inclusive Vacations.
    </p>
  </section>

</body>
</html>
```